Investment company needing business card

We are wanting a business card which looks sharp and easy on the eye. We are thinking of having a business card with the logo embossed on it, to really make it stand out. We will only have a small amount of information of the business card, person's name, position, email address and phone number

Contact Information for Business Card

Danielle Frost
Executive Assistant
+64 21 473 5162
danielf@harwickpartners.co.nz

Requirements
Must have
• Embossed logo
Should not have
• Not to be busy

```html
<!DOCTYPE html>
<html lang="en">
<head>
<meta charset="UTF-8">
<title>Harwick Partners – Business Card</title>
<link href="https://fonts.googleapis.com/css2?family=Lato:wght@400;700;900&display=swap" rel="stylesheet">
<style>
  :root {
    --brand-green: #23b573;
    --ink-grey: #444444;
    --rule-grey: #6b6b6b;
    --card-white: #ffffff;
    --backdrop: #e4e4e4;
  }
  * { margin: 0; padding: 0; box-sizing: border-box; }
  html, body {
    width: 1200px;
    height: 900px;
    overflow: hidden;
    background: var(--backdrop);
    font-family: "Lato", sans-serif;
  }
  .canvas {
    position: relative;
    width: 1200px;
    height: 900px;
  }
  .card {
    position: absolute;
    top: 170px;
    width: 345px;
    height: 560px;
    box-shadow: 3px 4px 8px rgba(0, 0, 0, 0.25);
    text-align: center;
  }
  .card--front { left: 260px; background: var(--card-white); }
  .card--back { left: 632px; background: var(--brand-green); }

  .brand-mark {
    position: absolute;
    left: 50%;
    transform: translateX(-50%);
  }
  .card--front .brand-mark {
    top: 56px;
    width: 94px;
    height: 94px;
    background: var(--brand-green);
  }
  .card--back .brand-mark {
    top: 290px;
    width: 134px;
    height: 134px;
    background: var(--card-white);
  }
  .brand-name {
    position: absolute;
    left: 0;
    right: 0;
    font-weight: 900;
    letter-spacing: 1px;
    white-space: nowrap;
  }
  .card--front .brand-name {
    top: 174px;
    font-size: 24px;
    color: var(--brand-green);
  }
  .card--back .brand-name {
    top: 454px;
    font-size: 28px;
    color: var(--card-white);
  }

  .holder {
    position: absolute;
    left: 0;
    right: 0;
    top: 380px;
  }
  .holder-name {
    font-size: 23px;
    font-weight: 700;
    letter-spacing: 0.5px;
    color: var(--brand-green);
    text-transform: uppercase;
    line-height: 30px;
  }
  .holder-role {
    font-size: 17px;
    color: var(--ink-grey);
    line-height: 22px;
  }
  .divider {
    width: 200px;
    height: 1px;
    margin: 18px auto 14px;
    background: var(--rule-grey);
  }
  .contact-line {
    font-size: 16px;
    color: var(--ink-grey);
    line-height: 23px;
  }
</style>
</head>
<body>
  <main class="canvas">
    <section class="card card--front" aria-label="Business card front">
      <div class="brand-mark"></div>
      <div class="brand-name">HARWICK PARTNERS</div>
      <div class="holder">
        <p class="holder-name">Danielle Frost</p>
        <p class="holder-role">Executive Assistant</p>
        <div class="divider"></div>
        <p class="contact-line">+64 21 473 5162</p>
        <p class="contact-line">danielf@harwickpartners.co.nz</p>
      </div>
    </section>

    <section class="card card--back" aria-label="Business card back">
      <div class="brand-mark"></div>
      <div class="brand-name">HARWICK PARTNERS</div>
    </section>
  </main>
</body>
</html>
```